K7 Electrical Services Ltd Web design

I require a web site for my new electrical contracting company. We are customer service orientated. Offering high value electrical installations, design and maintenance. Focused on custom residential and commercial upgrading. Lighting design and application are paramount in our company's services. Industry leading product use and integration are always on the forefront with our customer client services. As well as energy efficiency.

Target Market(s)

Homebuilders, General Contractors, Property management companies, clients, individuals,

Industry/Entity Type

Electric Company

Coding

Coded - Design and coding required

Number of Pages Required

3 page

Requirements
Must have
• Classic, modern, edgy but not trendy . Appeals to the masse.
• 3 page
• home page
• about page
• gallery page
• ability to contact from the webiste
Nice to have
• open to all types of designs that are relative to the construction industry.
• Black, Grey, metallic ice blue and deep purple colours from the logo.
Should not have
• anything cheesy with cartoon light bulb images.

```html
<!DOCTYPE html>
<html lang="en">
<head>
<meta charset="utf-8">
<title>K7 Electrical Services Ltd</title>
<link rel="stylesheet" href="https://fonts.googleapis.com/css2?family=Exo+2:wght@500;600;700&family=Open+Sans:wght@400;600;700&family=Cinzel:wght@400&display=swap">
<style>
:root{
  --purple:#5f2c91;
  --purple-dark:#4a2173;
  --grey-bg:#f1f1f1;
  --grey-text:#9a9a9a;
  --ink:#222;
  --body:#444;
  --night:#171b21;
  --footer-bar:#bdbdbd;
  --white:#fff;
}
*{box-sizing:border-box;margin:0;padding:0}
html,body{width:1200px;height:3261px;overflow:hidden;background:var(--white)}
body{position:relative;font-family:"Open Sans",Arial,sans-serif;color:var(--body)}
section,header,footer{position:absolute;left:0;width:1200px}
.abs{position:absolute}
.heading{font-family:"Exo 2",Arial,sans-serif;font-weight:700;text-align:center;text-transform:uppercase;font-size:36px;letter-spacing:1px}
.heading .accent{color:var(--purple)}
.heading .muted{color:var(--grey-text)}
.rule{position:absolute;left:552px;width:96px;height:4px;background:linear-gradient(90deg,var(--purple) 0 50%,#c9c9c9 50%)}
.photo{position:absolute}
.brand-name{font-family:"Exo 2",Arial,sans-serif;font-weight:700;color:var(--purple);letter-spacing:1px;text-transform:uppercase;text-align:center;line-height:1.1}

/* header / hero */
.hero{top:0;height:555px;overflow:hidden}
.hero-photo{left:0;top:0;width:1200px;height:555px;background:radial-gradient(ellipse at 40% 40%,#d9d6d0 0%,#a9a39a 40%,#5a5148 75%,#2a241f 100%)}
.topbar{left:0;top:0;width:1200px;height:104px;background:rgba(255,255,255,.55)}
.logo-top{left:141px;top:20px;width:220px;font-size:26px}
.logo-top small{display:block;font-size:12px;letter-spacing:5px;color:var(--purple)}
.schedule-link{left:817px;top:14px;font-family:"Exo 2",sans-serif;font-weight:700;font-size:14px;color:#111}
.nav{left:640px;top:62px;display:flex;gap:0}
.nav a{font-family:"Exo 2",sans-serif;font-weight:600;font-size:14px;color:#222;text-decoration:none;text-transform:uppercase;position:absolute;white-space:nowrap}
.nav a.active{color:var(--purple)}
.nav a.active::after{content:"";position:absolute;left:0;right:0;bottom:-8px;height:2px;background:var(--purple)}
.slide-arrow{top:283px;width:36px;height:30px;background:#2b2b2b;color:#fff;font-size:18px;display:flex;align-items:center;justify-content:center}
.hero-caption{left:200px;top:458px;width:800px;text-align:center;color:#fff;font-family:"Exo 2",sans-serif;font-size:30px;line-height:1.3;text-shadow:0 2px 6px rgba(0,0,0,.6)}
.hero-curve{left:0;top:490px}

/* intro */
.intro{top:555px;height:641px}
.intro-logo{left:450px;top:50px;width:300px;font-size:32px}
.intro-logo small{display:block;font-size:13px;letter-spacing:7px}
.intro-text{left:190px;top:132px;width:820px;font-size:14px;line-height:1.6;text-align:center}
.service-card{top:206px;height:370px}
.service-photo{left:0;top:0;width:100%;height:265px}
.service-box{position:absolute;left:18px;right:18px;top:208px;height:160px;background:#fff;box-shadow:0 2px 8px rgba(0,0,0,.15);text-align:center;padding-top:20px}
.service-box h3{font-family:"Exo 2",sans-serif;font-weight:600;font-size:17px;color:#111;line-height:1.25}
.service-box p{font-size:12px;line-height:1.5;margin:8px 14px 0}
.btn-small{display:inline-block;margin-top:12px;background:var(--purple);color:#fff;font-size:12px;padding:4px 28px;border-radius:14px}
.service-card.featured .service-box{background:var(--purple);color:#fff}
.service-card.featured .service-box h3{color:#fff}
.service-card.featured .btn-small{background:#fff;color:var(--purple)}

/* about */
.about{top:1196px;height:385px;background:var(--grey-bg)}
.about .heading{position:absolute;left:0;width:1200px;top:52px}
.about-text{left:140px;top:132px;width:920px;font-size:12px;line-height:1.75;text-align:center}
.about-text p+p{margin-top:8px}
.btn-call{left:490px;top:290px;width:196px;height:46px;background:var(--purple);color:#fff;font-family:"Exo 2",sans-serif;font-weight:600;font-size:20px;border-radius:8px;display:flex;align-items:center;justify-content:center}

/* why */
.why{top:1581px;height:332px;overflow:hidden}
.why-photo{left:0;top:0;width:1200px;height:332px;background:linear-gradient(180deg,#2a3138 0%,#1b2027 45%,#0e1014 100%)}
.why .heading{position:absolute;left:0;width:1200px;top:66px;color:#fff}
.why-text{left:150px;top:136px;width:900px;text-align:center;color:#eee;font-size:17px;line-height:2}
.why-cta{left:450px;top:216px;width:300px;text-align:center;color:#fff;font-family:"Exo 2",sans-serif;font-weight:600;font-size:16px;line-height:1.35;text-transform:uppercase}

/* gallery */
.gallery{top:1913px;height:505px}
.gallery .heading{position:absolute;left:0;width:1200px;top:72px}
.gal-arrow{top:250px;color:#999;font-size:60px;font-weight:300;line-height:1}
.gal-video{left:141px;top:148px;width:339px;height:272px;background:linear-gradient(160deg,#8ea3b8,#3f4c5e 60%,#20262f)}
.video-play{left:145px;top:112px}
.video-bar{left:0;bottom:0;width:339px;height:26px;background:rgba(0,0,0,.55)}
.gal-tile{background:linear-gradient(135deg,#8a7a6a,#3d342c)}
.tile-caption{left:10px;top:14px;width:160px;color:#fff;font-size:11px;line-height:1.4}

/* reviews */
.reviews{top:2418px;height:419px;background:var(--grey-bg)}
.reviews .heading{position:absolute;left:0;width:1200px;top:46px}
.review-photo{left:143px;top:141px;width:253px;height:213px;background:linear-gradient(135deg,#e7e2d8,#b9ad9a 60%,#7d705f);border:3px solid #222}
.review-text{left:430px;top:160px;width:630px;font-size:14px;line-height:1.8}
.review-name{left:430px;top:311px;width:630px;font-family:Cinzel,serif;font-size:13px;color:#222;display:flex;align-items:center;gap:14px}
.review-name::after{content:"";flex:1;height:1px;background:#ccc}

/* footer */
.footer{top:2837px;height:380px;background:var(--purple)}
.inquiry{left:141px;top:-11px;width:335px;height:344px;background:#fff;padding:28px 34px}
.inquiry h4{font-family:"Exo 2",sans-serif;font-weight:700;font-size:20px;color:#111;text-transform:uppercase}
.inquiry h4 span{color:var(--purple)}
.field{display:block;width:100%;height:32px;border:1px solid #ddd;margin-top:8px;font-size:10px;color:#aaa;padding:9px 8px;font-family:"Open Sans",sans-serif}
.inquiry .field:first-of-type{margin-top:20px}
.field.area{height:56px}
.btn-submit{margin-top:8px;height:32px;background:var(--purple);color:#fff;font-family:"Exo 2",sans-serif;font-weight:600;font-size:15px;text-transform:uppercase;display:flex;align-items:center;justify-content:center}
.foot-title{font-family:"Exo 2",sans-serif;font-weight:700;font-size:16px;color:#fff;text-transform:uppercase;padding-bottom:8px;border-bottom:1px solid rgba(255,255,255,.35)}
.foot-links{left:515px;top:72px;width:220px;color:#fff}
.foot-links ul{list-style:none;margin-top:10px}
.foot-links li{font-size:12px;line-height:26px}
.foot-links li::before{content:"› ";}
.follow{left:515px;top:228px;width:220px}
.social{display:flex;gap:9px;margin-top:14px}
.social span{width:26px;height:26px;border-radius:50%;background:#fff;opacity:.9}
.contact{left:778px;top:72px;width:280px;color:#fff}
.contact-row{display:flex;gap:14px;margin-top:16px;font-size:12px;line-height:1.5}
.contact-row svg{flex:none;margin-top:2px}
.copyright{top:3217px;height:44px;background:var(--footer-bar);font-size:11px;color:#333}
.copyright .left{left:147px;top:15px}
.copyright .right{left:850px;top:15px}
</style>
</head>
<body>

<header class="hero">
  <div class="abs hero-photo" role="img" aria-label="Photo of an electrician testing a breaker panel with a multimeter"></div>
  <div class="abs topbar"></div>
  <div class="abs brand-name logo-top">K7 Electrical<small>Services Ltd</small></div>
  <div class="abs schedule-link">SCHEDULE YOUR SERVICE TODAY</div>
  <nav class="abs nav">
    <a class="active" href="#" style="left:0">Home</a>
    <a href="#" style="left:127px">About Us</a>
    <a href="#" style="left:245px">Gallery</a>
    <a href="#" style="left:366px">Contact Us</a>
  </nav>
  <div class="abs slide-arrow" style="left:0">‹</div>
  <div class="abs slide-arrow" style="left:1164px">›</div>
  <div class="abs hero-caption">Offering High Value Electrical Installations, Design &amp; Maintenance</div>
  <svg class="abs hero-curve" width="1200" height="65" viewBox="0 0 1200 65" aria-hidden="true">
    <path d="M0 40 Q600 110 1200 0 L1200 65 L0 65Z" fill="#fff"/>
    <path d="M0 38 Q600 105 1200 0 L1200 10 Q600 118 0 52Z" fill="var(--purple)"/>
  </svg>
</header>

<section class="intro">
  <div class="abs brand-name intro-logo">K7 Electrical<small>Services Ltd</small></div>
  <p class="abs intro-text">We are customer service orientated. Offering high value text of the printing and typesetting industry. Lorem Ipsum has been the industry's standard dummy text ever since the 1500s.</p>

  <article class="abs service-card" style="left:141px;width:284px">
    <div class="photo service-photo" role="img" aria-label="Photo of wiring being tested with a multimeter" style="background:linear-gradient(135deg,#c9a34a,#7c5a2c 55%,#3e3022)"></div>
    <div class="service-box"><h3>Electrical<br>Installations</h3><p>Lorem ipsum dolor sit amet werew erer consectetuer adipiscing elit</p><span class="btn-small">Read More</span></div>
  </article>
  <article class="abs service-card featured" style="left:459px;width:266px">
    <div class="photo service-photo" role="img" aria-label="Photo of an electrician installing a chandelier" style="background:linear-gradient(180deg,#f2f2f2,#cfcac2 60%,#8f877c)"></div>
    <div class="service-box"><h3>Design<br>And Maintenance</h3><p>Lorem ipsum dolor sit amet werew erer consectetuer adipiscing elit</p><span class="btn-small">Read More</span></div>
  </article>
  <article class="abs service-card" style="left:776px;width:284px">
    <div class="photo service-photo" role="img" aria-label="Photo of a living room with recessed ceiling lights" style="background:linear-gradient(180deg,#d8d2c8,#8c6e52 60%,#4a3526)"></div>
    <div class="service-box"><h3>Lighting Design<br>And Application</h3><p>Lorem ipsum dolor sit amet werew erer consectetuer adipiscing elit</p><span class="btn-small">Read More</span></div>
  </article>
</section>

<section class="about">
  <h2 class="heading"><span class="accent">About</span> <span class="accent">K7</span> <span class="muted">Electrical</span></h2>
  <div class="rule" style="top:110px"></div>
  <div class="abs about-text">
    <p>Lorem ipsum dolor sit amet, consectetuer adipiscing elit, sed diam nonummy nibh euismod tincidunt ut laoreet dolore magna aliquam erat volutpat. Ut wisi enim ad minim veniam, quis nostrud exerci tation ullamcorper suscipit lobortis nisl ut aliquip ex ea commodo consequat.</p>
    <p>Lorem ipsum dolor sit amet, consectetuer adipiscing elit, sed diam nonummy nibh euismod tincidunt ut laoreet dolore magna aliquam erat volutpat. Ut wisi enim ad minim veniam, quis nostrud exerci tation ullamcorper suscipit lobortis nisl ut aliquip ex ea commodo consequat. Duis autem vel eum iriure dolor in hendrerit in vulputate velit esse molestie consequat, vel illum dolore eu feugiat nulla facilisis at vero eros et accumsan et iusto odio dignissim qui blandit praesent luptatum zzril delenit augue duis dolore te feugait nulla facilisi. Duis autem vel eum iriure dolor in hendrerit in vulputate velit esse molestie consequat, vel illum dolore eu feugiat nulla facilisis at vero eros et accumsan et iusto odio dignissim qui blandit praesent luptatum zzril delenit augue duis dolore te feugait nulla facilisi.</p>
  </div>
  <div class="abs btn-call">Call Us Today</div>
</section>

<section class="why">
  <div class="abs why-photo" role="img" aria-label="Night photo of a lit house across a lake"></div>
  <h2 class="heading"><span class="accent">Why Choose</span> Us</h2>
  <div class="rule" style="top:120px"></div>
  <p class="abs why-text">Lighting design and application are paramount in our company's services.<br>Industry leading product use &amp; integration are always on the forefront with our customer client services.</p>
  <div class="abs why-cta">Schedule<br>Your Service Today</div>
</section>

<section class="gallery">
  <h2 class="heading"><span class="accent">Work</span> <span class="muted">Gallery</span></h2>
  <div class="rule" style="top:122px"></div>
  <div class="abs gal-arrow" style="left:96px">‹</div>
  <div class="abs gal-arrow" style="left:1084px">›</div>
  <div class="abs gal-video" role="img" aria-label="Video still of an electrician working at a panel">
    <svg class="abs video-play" width="50" height="50" viewBox="0 0 50 50" aria-hidden="true"><circle cx="25" cy="25" r="24" fill="rgba(0,0,0,.6)"/><path d="M20 15 L36 25 L20 35Z" fill="#fff"/></svg>
    <div class="abs video-bar"></div>
  </div>
  <div class="abs gal-tile" style="left:491px;top:148px;width:183px;height:130px;background:linear-gradient(135deg,#4a4a4a,#1c1c1c)" role="img" aria-label="Photo of electrical work">
    <p class="abs tile-caption">Lorem ipsums is the dummy text of the industry is the dummy text of the.</p>
  </div>
  <div class="abs gal-tile" style="left:491px;top:289px;width:183px;height:131px;background:linear-gradient(135deg,#c79a63,#6b4a2c)" role="img" aria-label="Photo of an electrician in a timber frame building"></div>
  <div class="abs gal-tile" style="left:683px;top:148px;width:182px;height:272px;background:linear-gradient(160deg,#3a3f47,#c9a23a 55%,#2a2d33)" role="img" aria-label="Photo of a multimeter held at a panel"></div>
  <div class="abs gal-tile" style="left:876px;top:148px;width:183px;height:130px;background:linear-gradient(135deg,#e6dccb,#9b8466)" role="img" aria-label="Photo of an electrician installing a ceiling light"></div>
  <div class="abs gal-tile" style="left:876px;top:289px;width:183px;height:131px;background:linear-gradient(180deg,#e8e4dc,#a89a86)" role="img" aria-label="Photo of a bright office interior with ceiling lights"></div>
</section>

<section class="reviews">
  <h2 class="heading"><span class="accent">Happy Customer</span> <span class="muted">Reviews</span></h2>
  <div class="rule" style="top:98px"></div>
  <div class="abs gal-arrow" style="left:96px;top:182px">‹</div>
  <div class="abs gal-arrow" style="left:1084px;top:182px">›</div>
  <div class="abs review-photo" role="img" aria-label="Photo of a family in their new home"></div>
  <p class="abs review-text">Lorem ipsum dolor sit amet, consectetuer adipiscing elit, sed diam nonummy nibh euismod tincidunt ut laoreet dolore magna aliquam erat volutpat. Ut wisi enim ad minim veniam, quis nostrud exerci tation ullamcorper suscipit lobortis nisl ut aliquip ex ea commodo consequat. Duis autem vel eum iriure dolor in hendrerit in vulputate velit esse molestie consequat, vel illum dolore eu feugiat nulla facilisis at vero eros et.</p>
  <div class="abs review-name">-Daniel Morrow</div>
</section>

<footer class="footer">
  <form class="abs inquiry">
    <h4>Quick <span>Inquiry</span></h4>
    <span class="field">Name</span>
    <span class="field">Phone</span>
    <span class="field">Email</span>
    <span class="field area">Message</span>
    <div class="btn-submit">Submit Now</div>
  </form>
  <div class="abs foot-links">
    <div class="foot-title">Quick Links</div>
    <ul><li>Home</li><li>About Us</li><li>Gallery</li><li>Contact Us</li></ul>
  </div>
  <div class="abs follow">
    <div class="foot-title">Follow Us Today</div>
    <div class="social"><span></span><span></span><span></span><span></span><span></span></div>
  </div>
  <div class="abs contact">
    <div class="foot-title">Contact Details</div>
    <div class="contact-row"><svg width="14" height="18" viewBox="0 0 14 18" aria-hidden="true"><path d="M7 1C3.7 1 1 3.6 1 6.8 1 11 7 17 7 17s6-6 6-10.2C13 3.6 10.3 1 7 1z" fill="none" stroke="#fff" stroke-width="1.5"/><circle cx="7" cy="7" r="2" fill="#fff"/></svg><span>123-Orem ipsum dolor sit amet,<br>consectetuer, NC-123456</span></div>
    <div class="contact-row"><svg width="16" height="16" viewBox="0 0 16 16" aria-hidden="true"><path d="M3 1l3 3-2 2c1 2 3 4 5 5l2-2 3 3-2 3C7 14 2 9 1 3z" fill="none" stroke="#fff" stroke-width="1.4"/></svg><span>Phone<br>123-456-7905</span></div>
    <div class="contact-row"><svg width="16" height="12" viewBox="0 0 16 12" aria-hidden="true"><rect x="1" y="1" width="14" height="10" fill="none" stroke="#fff" stroke-width="1.4"/><path d="M1 1l7 6 7-6" fill="none" stroke="#fff" stroke-width="1.4"/></svg><span>Email<br>inquiry@k7electricalservices.com</span></div>
  </div>
</footer>

<div class="abs copyright" style="left:0;width:1200px">
  <span class="abs left">Copyright © K7ElectricalServices - 2018. All Rights Reserved.</span>
  <span class="abs right">Privacy Policy &nbsp;|&nbsp; Terms And Conditions</span>
</div>

</body>
</html>
```